Biker App Design
Zielgruppe
VolnaPex erstellt eine App für Biker mit der:
- Motorradfahrer andere Biker finden können um gemeinsam zu fahren
- Motorradfahrer ihre Strecke tracken können um Punkte zu sammeln
- Biker können mit diesen Punkten Ränge aufsteigen 'Masterbiker, Anfänger, GuruFahrer, etc.', es soll eine Art 'Erfahrungsleiste' angezeigt werden
- Diese Punkte können gegen Gutscheine/Wertsachen eingelöst werden
- Es gibt Nachrichten (Art Blogeinträge) genau zu diesen Themen
Aufgabenstellung
Modernes Design
Reduziert
Es werden folgende Screens benötigt:
Startbild
Start - Dateneintragen:
Um den Fahrer besser mit anderen Fahren zu verknüpfen muss er folgende informationen angeben:
- Welche Art Motorrad fährt er? Sport, Vintage, Cross
- Männlich/Weiblich/Divers
- Geburtsjahr
- PLZ des Heimatorts
- Nickname
Startscreen um andere Biker zu suchen und damit eine Tour zu starten
- Hier sollte ein 'Map' Bild mit einem Kreis für den Umkreis dargestellt werden + Pins mit Personenbilder , welche
Personen in der Nähe sind und auch fahren möchten
- Hier sollte stehen, wieviel Punkte er noch benötigt um den nächsten Gutschein freizuschalten
Screen zum Start des Trackens
Screen während dem Tracken mit Pause/Stop-Option
Screen mit einem Überblick der neuen Blogeinträge
Screen beim beenden des Trackens (Strecke speichern, Bild hinzufügen, Freunde informieren ich bin angekommen)
Screen Profilseite, Bild des Bikers + Bike + Erfahrungspunkte + gesammelte Errungenschaften z.B. 'Mit 3 Freunden mehr als 1000km gefahren'
Screen Bestenliste, anhand der Punkte
Es sollen Dateiformate verwendet werden, die gut wiederverwendet werden können. Es sollen sich Bausteine aus diesen Design wiederverwenden lassen können.

```html
<!DOCTYPE html>
<html lang="en">
<head>
<meta charset="utf-8">
<title>VolnaPex Biker App – Profile</title>
<link rel="stylesheet" href="https://fonts.googleapis.com/css2?family=Exo+2:wght@400;500;600;700&family=Roboto:wght@300;400;500&display=swap">
<style>
  :root {
    --stage: #1b1f24;
    --screen: #2b2c2e;
    --screen-dark: #232425;
    --panel: #333436;
    --panel-light: #3b3c3e;
    --text: #f2f2f2;
    --muted: #9a9b9d;
    --dim: #5d5e60;
    --green: #3fae2a;
    --green-text: #3fcf3a;
    --red: #e8333a;
  }
  * { box-sizing: border-box; margin: 0; padding: 0; }
  html, body { width: 1200px; height: 801px; overflow: hidden; }
  body {
    background: var(--stage);
    font-family: "Roboto", sans-serif;
    color: var(--text);
    display: flex; align-items: center; justify-content: center;
  }
  .app-screen {
    position: relative;
    width: 372px; height: 761px;
    background: var(--screen);
    overflow: hidden;
    border-radius: 6px;
  }
  .status-bar {
    height: 26px; background: var(--screen-dark);
    display: flex; justify-content: flex-end; align-items: center; gap: 6px;
    padding: 0 12px; font-size: 13px;
  }
  .status-bar svg { fill: var(--text); }
  .top-bar {
    height: 48px; display: flex; align-items: center; padding: 0 16px;
  }
  .top-bar .actions { margin-left: auto; display: flex; gap: 18px; }
  .icon { stroke: var(--dim); fill: none; stroke-width: 1.8; }

  .profile { display: flex; gap: 14px; padding: 4px 16px 14px; }
  .profile-photo {
    flex: none; width: 96px; height: 96px; border-radius: 50%;
    background: radial-gradient(circle at 50% 30%, #cfe3f2, #6e8aa5 60%, #3a4048);
  }
  .profile-name { font-family: "Exo 2", sans-serif; font-weight: 600; font-size: 24px; line-height: 1.1; }
  .profile-place { font-size: 9px; color: var(--muted); margin: 3px 0 6px; }
  .profile-bio { font-size: 9.5px; color: var(--muted); font-weight: 300; line-height: 1.35; }

  .bike-band {
    position: relative; height: 50px; background: var(--panel);
    display: flex; align-items: center;
  }
  .bike-flag { width: 60px; height: 50px; background: var(--green); clip-path: polygon(0 0,100% 0,70% 100%,0 100%); }
  .bike-name { font-family: "Exo 2", sans-serif; font-weight: 600; font-size: 15px; margin-left: 20px; }
  .edit-bike {
    position: absolute; right: 0; top: -10px; height: 42px; width: 150px;
    background: var(--panel-light); clip-path: polygon(10% 0,100% 0,100% 100%,0 100%);
    font-size: 13px; display: flex; align-items: center; justify-content: center;
  }

  .rank { padding: 10px 16px 0; position: relative; }
  .rank-title { font-family: "Exo 2", sans-serif; font-weight: 700; font-size: 19px; }
  .rank-points {
    position: absolute; right: 16px; top: 2px; text-align: right;
    font-family: "Exo 2", sans-serif; color: var(--green-text); font-weight: 700; font-size: 22px; line-height: 1;
  }
  .rank-points small { display: block; font-size: 11px; color: var(--muted); font-weight: 500; }
  .xp-bar { display: flex; gap: 6px; margin-top: 10px; }
  .xp-bar span {
    flex: 1; height: 10px; background: var(--panel-light);
    transform: skewX(-25deg);
  }
  .xp-bar span.filled { background: var(--red); }
  .xp-label { font-size: 7px; color: var(--muted); margin-top: 6px; }

  .achievements { text-align: center; padding: 4px 16px 0; }
  .achievements h3 { font-family: "Exo 2", sans-serif; font-size: 14px; font-weight: 600; }
  .achievement-list { display: flex; justify-content: space-between; margin-top: 12px; }
  .achievement { width: 100px; display: flex; flex-direction: column; align-items: center; gap: 6px; font-size: 7px; line-height: 1.3; }
  .achievement svg { stroke: var(--green-text); fill: none; stroke-width: 1.6; }

  .drives-title { text-align: center; color: var(--muted); font-size: 14px; margin: 16px 0 10px; }
  .drive-card {
    display: flex; height: 138px; background: var(--panel);
  }
  .drive-map { width: 112px; background: linear-gradient(135deg, #3c3d3f, #27282a); }
  .drive-info { flex: 1; padding: 12px 14px; display: flex; flex-direction: column; }
  .drive-route { font-family: "Exo 2", sans-serif; font-weight: 600; font-size: 16px; }
  .drive-date { font-size: 8px; margin-top: 6px; }
  .drive-stats { margin-top: auto; display: flex; justify-content: space-between; }
  .stat small { display: block; font-size: 7px; color: var(--muted); }
  .stat b { font-family: "Exo 2", sans-serif; font-size: 16px; font-weight: 600; }
  .drive-card.peek { height: 40px; margin-top: 6px; }
  .drive-card.peek .drive-info { padding-top: 10px; }

  .bottom-nav {
    position: absolute; left: 0; right: 0; bottom: 0; height: 58px;
    background: var(--screen-dark);
    display: flex; justify-content: space-around; align-items: center;
  }
  .bottom-nav .active { stroke: var(--red); }
</style>
</head>
<body>
<main class="app-screen">
  <div class="status-bar">
    <svg width="12" height="10" viewBox="0 0 12 10"><path d="M0 2 Q6 -2 12 2 L6 10Z"/></svg>
    <svg width="10" height="10" viewBox="0 0 10 10"><path d="M10 0V10H0Z"/></svg>
    <svg width="6" height="11" viewBox="0 0 6 11"><rect width="6" height="11" rx="1"/></svg>
    <span>12:30</span>
  </div>

  <header class="top-bar">
    <svg class="icon" width="22" height="16" viewBox="0 0 22 16"><path d="M1 2H21M1 8H21M1 14H21"/></svg>
    <div class="actions">
      <svg class="icon" width="20" height="20" viewBox="0 0 20 20"><circle cx="8" cy="8" r="6"/><path d="M12.5 12.5L19 19"/></svg>
      <svg class="icon" width="20" height="20" viewBox="0 0 20 20"><path d="M4 15V9a6 6 0 0 1 12 0v6H3h14M8 18h4"/></svg>
      <svg class="icon" width="20" height="20" viewBox="0 0 20 20"><circle cx="10" cy="10" r="3"/><circle cx="10" cy="10" r="7" stroke-dasharray="3 2"/></svg>
    </div>
  </header>

  <section class="profile">
    <div class="profile-photo" role="img" aria-label="Portrait photo of the rider sitting on his motorbike"></div>
    <div>
      <h1 class="profile-name">Jan Mertel</h1>
      <p class="profile-place">Sydney, NSW, Australia</p>
      <p class="profile-bio">"Lorem ipsum dolor sit amet, consectetur adipisicing elit, sed do eiusmod tempor incididunt ut labore et dolore magna aliqua. Ut enim ad minim veniam, quis nostrud exercitation ullamco laboris</p>
    </div>
  </section>

  <section class="bike-band">
    <div class="bike-flag"></div>
    <span class="bike-name">Kuroda KX 1000</span>
    <span class="edit-bike">Edit bike</span>
  </section>

  <section class="rank">
    <h2 class="rank-title">Guru Driver</h2>
    <p class="rank-points">1892<small>pts</small></p>
    <div class="xp-bar"><span class="filled"></span><span class="filled"></span><span></span><span></span><span></span></div>
    <p class="xp-label">Experience level</p>
  </section>

  <section class="achievements">
    <h3>Buy more!</h3>
    <div class="achievement-list">
      <div class="achievement">
        <svg width="22" height="22" viewBox="0 0 24 24"><path d="M12 2l3 7h7l-5.5 4.5 2 7.5L12 16.5 5.5 21l2-7.5L2 9h7z"/></svg>
        With 3 friends driven more than 1000km
      </div>
      <div class="achievement">
        <svg width="22" height="22" viewBox="0 0 24 24"><path d="M12 2l3 7h7l-5.5 4.5 2 7.5L12 16.5 5.5 21l2-7.5L2 9h7z"/></svg>
        7 countries
      </div>
      <div class="achievement">
        <svg width="22" height="22" viewBox="0 0 24 24"><path d="M12 2l3 7h7l-5.5 4.5 2 7.5L12 16.5 5.5 21l2-7.5L2 9h7z"/></svg>
        3 years on wheels
      </div>
    </div>
  </section>

  <h3 class="drives-title">Drives</h3>
  <article class="drive-card">
    <div class="drive-map" role="img" aria-label="Map of the route along the coast"></div>
    <div class="drive-info">
      <h4 class="drive-route">Sydney - Gaffneys Creek</h4>
      <p class="drive-date">24.12.2019</p>
      <div class="drive-stats">
        <p class="stat"><small>Start at</small><b>14:43</b></p>
        <p class="stat"><small>End at</small><b>14:43</b></p>
        <p class="stat"><small>Distance</small><b>464.2km</b></p>
      </div>
    </div>
  </article>
  <article class="drive-card peek">
    <div class="drive-map" role="img" aria-label="Map of the route"></div>
    <div class="drive-info"><h4 class="drive-route">Melbourne - Phillip Island</h4></div>
  </article>

  <nav class="bottom-nav">
    <svg class="icon" width="24" height="24" viewBox="0 0 24 24"><path d="M3 5l6-2 6 2 6-2v16l-6 2-6-2-6 2zM9 3v16M15 5v16"/></svg>
    <svg class="icon" width="24" height="24" viewBox="0 0 24 24"><path d="M5 22V3h12l-3 4 3 4H5"/></svg>
    <svg class="icon" width="24" height="24" viewBox="0 0 24 24"><circle cx="12" cy="12" r="9"/></svg>
    <svg class="icon" width="24" height="24" viewBox="0 0 24 24"><rect x="3" y="7" width="14" height="14" rx="2"/><path d="M7 7V3h14v14h-4"/></svg>
    <svg class="icon active" width="24" height="24" viewBox="0 0 24 24"><circle cx="12" cy="8" r="4"/><path d="M4 22c0-5 3.5-8 8-8s8 3 8 8"/></svg>
  </nav>
</main>
</body>
</html>
```